Emberlane Air Business Card Design

Design new, 2 sides, business cards for a residential and light commercial heating, air conditioning contractor.

Target Market(s)

Homeowners, small businesses

Industry/Entity Type

Business

Contact Information for Business Card

Dominic Westerhall
Phone - 862-415-2736
Email
Address - PO box 518
Brightwater NJ 07912
Website - www.HarborBreezeLLC.example

Requirements
Must have
• logo, company colors, standard size with no die cut, so I can use nova stamp

```html
<!DOCTYPE html>
<html lang="en">
<head>
<meta charset="utf-8">
<title>Emberlane Air Business Card</title>
<link rel="stylesheet" href="https://fonts.googleapis.com/css2?family=EB+Garamond:ital,wght@0,400;0,700;1,400&display=swap">
<style>
  :root {
    --brand-red: #9b1f32;
    --brand-orange: #f38b2f;
    --brand-cream: #fde79a;
    --tagline-gold: #f2c36b;
    --card-white: #ffffff;
    --ink-grey: #4a4a4a;
    --backdrop: #e9e7e4;
    --red-faint: #a8283b;
  }
  * { box-sizing: border-box; margin: 0; padding: 0; }
  html, body {
    width: 1200px; height: 576px; overflow: hidden;
    background: var(--backdrop);
    font-family: "EB Garamond", Georgia, serif;
  }
  .sheet {
    position: relative; width: 1200px; height: 576px;
    display: flex; align-items: center; justify-content: center; gap: 40px;
  }
  .card {
    position: relative; width: 540px; height: 309px; overflow: hidden;
    box-shadow: 0 6px 18px rgba(0,0,0,0.18);
  }

  /* Front side */
  .card--front { background: var(--card-white); }
  .chevron { position: absolute; inset: 0; width: 100%; height: 100%; }
  .brand-lockup {
    position: absolute; left: 36px; top: 52px;
    display: flex; align-items: center; gap: 10px;
  }
  .brand-lockup__dot {
    width: 14px; height: 14px; border-radius: 50%; background: var(--brand-orange);
  }
  .brand-lockup__name {
    font-size: 32px; font-weight: 700; color: var(--brand-red);
    text-transform: uppercase; letter-spacing: 1px; line-height: 1;
    white-space: nowrap;
  }
  .person {
    position: absolute; right: 118px; top: 134px; text-align: right;
  }
  .person__name {
    font-size: 22px; font-weight: 700; color: var(--brand-red);
    text-transform: uppercase; letter-spacing: 0.5px; line-height: 1.05;
    white-space: nowrap;
  }
  .person__title { font-size: 16px; color: var(--brand-orange); line-height: 1.2; }
  .contact {
    position: absolute; left: 36px; top: 196px;
    font-size: 14.5px; line-height: 1.5; color: var(--ink-grey);
    white-space: nowrap;
  }
  .contact__label { color: var(--brand-red); font-weight: 700; margin-right: 3px; }
  .contact__gap { display: inline-block; width: 12px; }

  /* Back side */
  .card--back {
    background: var(--brand-red);
    display: flex; flex-direction: column; align-items: center; justify-content: center;
  }
  .back-mark {
    font-size: 48px; font-weight: 700; color: var(--red-faint);
    text-transform: uppercase; letter-spacing: 2px; line-height: 1;
    white-space: nowrap;
  }
  .tagline {
    margin-top: 44px; text-align: center;
    font-style: italic; font-size: 17px; line-height: 1.3; color: var(--tagline-gold);
  }
</style>
</head>
<body>
<main class="sheet">
  <section class="card card--front" aria-label="Front of business card">
    <svg class="chevron" viewBox="0 0 540 309" preserveAspectRatio="none" aria-hidden="true">
      <polygon points="412,0 540,0 540,309 412,309 462,155" fill="var(--brand-orange)"/>
      <polygon points="444,0 540,0 540,309 444,309 494,155" fill="var(--brand-cream)"/>
      <polygon points="454,0 540,0 540,309 454,309 504,155" fill="var(--brand-orange)"/>
      <polygon points="474,0 540,0 540,309 474,309 524,155" fill="var(--brand-red)"/>
    </svg>
    <div class="brand-lockup">
      <span class="brand-lockup__dot"></span>
      <span class="brand-lockup__name">Emberlane Air</span>
    </div>
    <div class="person">
      <p class="person__name">Dominic Westerhall</p>
      <p class="person__title">CEO/Founder</p>
    </div>
    <div class="contact">
      <p><span class="contact__label">(a)</span> PO box 518, Brightwater NJ 07912</p>
      <p><span class="contact__label">(p)</span> 862-415-2736<span class="contact__gap"></span><span class="contact__label">(e)</span> dominic@emberlaneair.example</p>
      <p><span class="contact__label">(c)</span> 862-415-2790<span class="contact__gap"></span><span class="contact__label">(w)</span> www.EmberlaneAirLLC.example</p>
    </div>
  </section>

  <section class="card card--back" aria-label="Back of business card">
    <p class="back-mark">Emberlane Air</p>
    <p class="tagline">Residential &amp; Light Commercial<br>Heating &amp; Air conditioning</p>
  </section>
</main>
</body>
</html>
```